Sparrow Haulage needs a business card design.

Design a double-sided business card for new freight business. On the front, would like to see our logo along with the following info:

Martin Obuya
CEO/FOUNDER
555-206-7142
martinobuya@sparrow-haulage.example

On the reverse side, we would like to use the graphic image of our logo only without the Sparrow Haulage name.

```html
<!DOCTYPE html>
<html lang="en">
<head>
<meta charset="utf-8">
<title>Sparrow Haulage – Business Card</title>
<link href="https://fonts.googleapis.com/css2?family=Nunito+Sans:wght@400;700;800&display=swap" rel="stylesheet">
<style>
  :root {
    --backdrop: #dcdde1;
    --card-white: #ffffff;
    --navy: #1b1853;
    --navy-soft: #262366;
    --red: #b71c2b;
    --ink: #3b3b3b;
  }
  * { margin: 0; padding: 0; box-sizing: border-box; }
  html, body { width: 1200px; height: 859px; overflow: hidden; }
  body {
    background: var(--backdrop);
    font-family: "Nunito Sans", Arial, sans-serif;
    position: relative;
  }
  .card {
    position: absolute;
    left: 319px;
    width: 562px;
    height: 321px;
  }
  .card--front { top: 69px; background: var(--card-white); }
  .card--back { top: 470px; background: var(--navy); }

  .brand {
    position: absolute;
    left: 36px;
    top: 161px;
    transform: translateY(-50%);
    display: flex;
    align-items: center;
    gap: 10px;
  }
  .brand__dot {
    width: 36px; height: 36px;
    border-radius: 50%;
    background: var(--red);
    flex: none;
  }
  .brand__name {
    font-weight: 800;
    font-size: 20px;
    letter-spacing: 3.5px;
    line-height: 1.1;
    color: var(--navy);
    text-transform: uppercase;
  }

  .divider {
    position: absolute;
    left: 269px;
    top: 113px;
    width: 1.5px;
    height: 97px;
    background: var(--navy);
  }

  .contact { position: absolute; left: 290px; top: 107px; }
  .contact__name {
    font-weight: 800;
    font-size: 20px;
    color: var(--navy);
    line-height: 1;
  }
  .contact__name .surname { color: var(--red); }
  .contact__role {
    font-size: 12px;
    color: var(--ink);
    margin-top: 4px;
    letter-spacing: 0.2px;
  }
  .contact__list { list-style: none; margin-top: 13px; }
  .contact__item {
    display: flex;
    align-items: center;
    gap: 6px;
    font-size: 12.5px;
    color: var(--ink);
    height: 18px;
    white-space: nowrap;
  }
  .contact__icon { width: 10px; height: 10px; flex: none; fill: var(--red); }

  .back-mark {
    position: absolute;
    left: 50%;
    top: 50%;
    width: 170px;
    height: 170px;
    transform: translate(-50%, -50%);
    border-radius: 50%;
    background: var(--navy-soft);
  }
</style>
</head>
<body>
  <section class="card card--front">
    <div class="brand">
      <span class="brand__dot"></span>
      <span class="brand__name">Sparrow<br>Haulage</span>
    </div>
    <div class="divider"></div>
    <div class="contact">
      <p class="contact__name">Martin <span class="surname">Obuya</span></p>
      <p class="contact__role">CEO/FOUNDER</p>
      <ul class="contact__list">
        <li class="contact__item">
          <svg class="contact__icon" viewBox="0 0 10 10" aria-hidden="true"><path d="M2 0.5 L3.6 2.6 L2.8 3.6 Q3.8 5.8 6.2 7.1 L7.3 6.3 L9.5 7.9 L8.4 9.5 Q2.6 9 0.6 1.6 Z"/></svg>
          555-206-7142
        </li>
        <li class="contact__item">
          <svg class="contact__icon" viewBox="0 0 10 10" aria-hidden="true"><path d="M0 2 H10 V8.5 H0 Z M0.8 2.6 L5 5.6 L9.2 2.6 V3.4 L5 6.4 L0.8 3.4 Z" fill-rule="evenodd"/></svg>
          martinobuya@sparrow-haulage.example
        </li>
        <li class="contact__item">
          <svg class="contact__icon" viewBox="0 0 10 10" aria-hidden="true"><circle cx="5" cy="5" r="4.6"/><path d="M2.5 3 Q4 2.5 4.5 4 Q3.5 5.5 5 6.5 L4.5 8.5" stroke="#fff" stroke-width="0.8" fill="none"/></svg>
          www.sparrow-haulage.example
        </li>
      </ul>
    </div>
  </section>

  <section class="card card--back">
    <span class="back-mark"></span>
  </section>
</body>
</html>
```